Corvane Business Cards

Front of business card will have logo, name, address, & telephone number. Back of card will have a list of services provided - Roads, Substation Pads, Temporary Pads, Site Pads, Land Leveling, Powerline Row Cleaning, Land Clearing, Gates, Fencing, Construction Entrances, Excavation, Trenching, Underground Utilities, Directional Boring, Pile Driving. We are a construction company that uses heavy equipment like bulldozers, motor graders/blades, dump trucks, backhoes, hydro axes, & skid loaders. We build roads, pads, & install electric utility lines & waterlines underground. This logo is new. The word "Construction" can be smaller as uploaded 2 example edited logos. We will be using this card design for many employees.
Target Market(s)
Industrial Electric Powerline, Wind Turbine, Solar Panel, & Water Utility companies.
Contact Information for Business Card
Name/Position - Dwayne Halster - Owner
Address: 4875 FM 309
Brayford, OK 73521
Phone number - (580) 482-5096

```html
<!DOCTYPE html>
<html lang="en">
<head>
<meta charset="utf-8">
<title>Corvane Business Cards</title>
<link rel="stylesheet" href="https://fonts.googleapis.com/css2?family=Poppins:wght@400;700&display=swap">
<style>
  :root {
    --backdrop: #e9e6e3;
    --card-light: #f4f4f4;
    --card-dark: #3d0a16;
    --maroon: #3d0a16;
    --ink: #111111;
    --muted: #555555;
    --accent: #c8234f;
  }
  * { margin: 0; padding: 0; box-sizing: border-box; }
  html, body {
    width: 1125px;
    height: 1200px;
    overflow: hidden;
    background: var(--backdrop);
    font-family: "Poppins", sans-serif;
  }
  .sheet {
    position: relative;
    width: 1125px;
    height: 1200px;
  }
  .card {
    position: absolute;
    left: 150px;
    width: 825px;
    height: 470px;
    border-radius: 24px;
  }
  .card--front {
    top: 98px;
    background: var(--card-light);
  }
  .card--back {
    top: 632px;
    background: var(--card-dark);
  }
  .brand-mark {
    position: absolute;
    top: 84px;
    right: 62px;
    display: flex;
    align-items: center;
    gap: 10px;
  }
  .brand-mark__square {
    width: 18px;
    height: 18px;
    background: var(--maroon);
  }
  .brand-mark__name {
    font-weight: 700;
    font-size: 40px;
    letter-spacing: 1px;
    color: var(--maroon);
    line-height: 1;
  }
  .contact {
    position: absolute;
    left: 57px;
    top: 278px;
  }
  .contact__name {
    font-weight: 700;
    font-size: 25px;
    color: var(--maroon);
    line-height: 1.1;
    text-transform: uppercase;
  }
  .contact__role {
    font-weight: 400;
    font-size: 18px;
    color: var(--ink);
    line-height: 1.2;
  }
  .contact__details {
    margin-top: 18px;
    font-style: normal;
    font-weight: 400;
    font-size: 18px;
    color: var(--muted);
    line-height: 1.35;
  }
  .back-brand {
    position: absolute;
    inset: 0;
    display: flex;
    flex-direction: column;
    align-items: center;
    justify-content: center;
    gap: 40px;
    color: var(--accent);
    font-weight: 700;
    text-transform: uppercase;
    text-align: center;
    line-height: 1;
  }
  .back-brand__name {
    font-size: 72px;
    letter-spacing: 2px;
  }
  .back-brand__trade {
    font-size: 36px;
    letter-spacing: 2px;
  }
</style>
</head>
<body>
  <main class="sheet">
    <section class="card card--front" aria-label="Business card front">
      <div class="brand-mark">
        <span class="brand-mark__square"></span>
        <span class="brand-mark__name">CORVANE</span>
      </div>
      <div class="contact">
        <p class="contact__name">Dwayne Halster</p>
        <p class="contact__role">Owner</p>
        <address class="contact__details">
          4875 FM 309<br>
          Brayford, OK 73521<br>
          (580) 482-5096
        </address>
      </div>
    </section>

    <section class="card card--back" aria-label="Business card back">
      <div class="back-brand">
        <p class="back-brand__name">Corvane</p>
        <p class="back-brand__trade">Construction</p>
      </div>
    </section>
  </main>
</body>
</html>
```